Bramblewood Card Company Business Cards

We are a trading card store with Glimmorax, sports and other TCG cards, we need a business card design that encompasses a clean cut, modern style with a retro flare. website is bramblewoodcardco.com for reference. Can utilize a comic book era feel or a more modern outdoor feel to utilize the "Pacific Northwest" elements of tress, mountains, etc.

Industry/Entity Type

Trading cards and collectibles

Contact Information for Business Card

business name, email address, phone number, name, owner job title

Font styles to use
Sans Serif

```html
<!DOCTYPE html>
<html lang="en">
<head>
<meta charset="utf-8">
<title>Bramblewood Card Company – Business Cards</title>
<link href="https://fonts.googleapis.com/css2?family=Lato:wght@400;700;900&display=swap" rel="stylesheet">
<style>
  :root {
    --bg: #2a2a2a;
    --card-grey: #757575;
    --card-black: #000000;
    --mountain-grey: #747474;
    --accent: #12bde0;
    --white: #ffffff;
    --icon-grey: #8a8a8a;
  }
  * { box-sizing: border-box; margin: 0; padding: 0; }
  html, body { width: 1200px; height: 689px; overflow: hidden; background: var(--bg); }
  body { position: relative; font-family: "Lato", sans-serif; }

  .card {
    position: absolute;
    top: 196px;
    width: 520px;
    height: 297px;
    border-radius: 22px;
    overflow: hidden;
  }
  .card--front { left: 50px; background: var(--card-grey); }
  .card--back { left: 630px; background: var(--card-black); }

  .brand {
    position: absolute;
    display: flex;
    align-items: center;
    gap: 10px;
    color: var(--white);
    font-weight: 900;
    text-transform: uppercase;
    letter-spacing: 0.04em;
    line-height: 1.05;
  }
  .brand__dot {
    flex: none;
    border-radius: 50%;
    background: var(--accent);
  }
  .card--front .brand { left: 50%; top: 50%; transform: translate(-50%, -50%); font-size: 26px; }
  .card--front .brand__dot { width: 22px; height: 22px; }
  .card--back .brand { right: 26px; top: 30px; font-size: 13px; }
  .card--back .brand__dot { width: 12px; height: 12px; }

  .scenery {
    position: absolute;
    right: 0;
    bottom: 0;
    width: 236px;
    height: 180px;
    background: linear-gradient(160deg, #8a8a8a 0%, var(--mountain-grey) 55%, #6a6a6a 100%);
  }

  .contact {
    position: absolute;
    left: 34px;
    top: 118px;
    width: 240px;
    color: var(--white);
  }
  .contact__name {
    color: var(--accent);
    font-size: 25px;
    font-weight: 400;
    letter-spacing: 0.01em;
    text-transform: uppercase;
    white-space: nowrap;
  }
  .contact__title { font-size: 15px; margin-top: 2px; }
  .contact__list { list-style: none; margin-top: 14px; }
  .contact__item {
    display: flex;
    align-items: center;
    gap: 10px;
    font-size: 14px;
    line-height: 22px;
    white-space: nowrap;
  }
  .contact__icon { width: 14px; height: 14px; flex: none; }
</style>
</head>
<body>

  <section class="card card--front" aria-label="Business card front">
    <div class="brand">
      <span class="brand__dot"></span>
      <span>Bramblewood<br>Card Company</span>
    </div>
  </section>

  <section class="card card--back" aria-label="Business card back">
    <div class="brand">
      <span class="brand__dot"></span>
      <span>Bramblewood<br>Card Company</span>
    </div>

    <div class="scenery" role="img" aria-label="Stylised grey mountain range with white snow peaks"></div>

    <div class="contact">
      <h1 class="contact__name">Marcus Reid</h1>
      <p class="contact__title">Managing Director</p>
      <ul class="contact__list">
        <li class="contact__item">
          <svg class="contact__icon" viewBox="0 0 16 16" aria-hidden="true">
            <path fill="var(--icon-grey)" d="M3.5 1.5l2.5 3-1.5 1.5c.8 1.8 2.2 3.2 4 4l1.5-1.5 3 2.5-1.5 2.5C7 13 3 9 1 4z"/>
          </svg>
          <span>044-987 654 321</span>
        </li>
        <li class="contact__item">
          <svg class="contact__icon" viewBox="0 0 16 16" aria-hidden="true">
            <rect x="1" y="3" width="14" height="10" fill="var(--icon-grey)"/>
            <path d="M1 3l7 6 7-6" fill="none" stroke="var(--card-black)" stroke-width="1.2"/>
          </svg>
          <span>info@bramblemail.com</span>
        </li>
        <li class="contact__item">
          <svg class="contact__icon" viewBox="0 0 16 16" aria-hidden="true">
            <circle cx="8" cy="8" r="7" fill="var(--icon-grey)"/>
            <path d="M1 8h14M8 1c-3 3-3 11 0 14M8 1c3 3 3 11 0 14" fill="none" stroke="var(--card-black)" stroke-width="1"/>
          </svg>
          <span>www.bramblewoodcardco.com</span>
        </li>
      </ul>
    </div>
  </section>

</body>
</html>
```